Locksmith Business Cards

My father-in-law is in need of new business cards for his locksmith business and I need to impress him. Kindly help me out!

You can see the previous business card attached. It is a family run business in North Wales.

No individual names on the cards.

Key Things to Feature:
- The words "Prompt", "Local", "Reliable" (as you can see under the logo on the website)
- 24h Emergency Service
- Covering All of North Wales, the Wirral and Chester
- The color blue
- A key or a lock would be interesting (similar to the ones that come up when you google locksmith business card)

Optional (only if design includes bullet points, like the example below):
https://imgvaultcdn.net/samples/208314/55172/55172_3904821_208314_image.jpg
- Residential / Commercial / Automotive
- Alarms & Cameras
- Key Cutting & Safes

https://www.brynhafod-locksmiths.co.uk/

Industry/Entity Type

Locksmith

Contact Information for Business Card

01632 960 418
07700 900 362
brynhafodlocksmiths@mailvane.com
Brynhafod Locksmiths, The Willow Barn, 7 Tannery Rd., Llandudno LL99 4QX
www.brynhafod-locksmiths.co.uk

Requirements
Must have
• - The words "Prompt", "Local", "Reliable" (as you can see under the logo on the website)
• - 24h Emergency Service
• - Covering All of North Wales, the Wirral and Chester
Nice to have
• - A key or a lock would be interesting (similar to the ones that come up when you google locksmith business card)

```html
<!DOCTYPE html>
<html lang="en">
<head>
<meta charset="utf-8">
<title>Brynhafod Locksmiths – Business Card</title>
<link rel="stylesheet" href="https://fonts.googleapis.com/css2?family=Oswald:wght@500&family=Source+Sans+3:wght@400;600&display=swap">
<style>
  :root {
    --backdrop: #5b5b5b;
    --paper: #ffffff;
    --navy: #1e2761;
    --ink: #222222;
    --white: #ffffff;
  }
  * { box-sizing: border-box; margin: 0; padding: 0; }
  html, body { width: 1200px; height: 900px; overflow: hidden; }
  body {
    background: var(--backdrop);
    position: relative;
    font-family: "Source Sans 3", "Myriad Pro", sans-serif;
    color: var(--ink);
  }
  .card {
    position: absolute;
    top: 200px;
    width: 310px;
    height: 502px;
  }
  .card--front {
    left: 253px;
    background: var(--paper);
    border-radius: 58px 0 58px 0;
  }
  .card--back {
    left: 627px;
    background: var(--navy);
    border-radius: 0 58px 0 58px;
    color: var(--white);
  }
  .brand {
    position: absolute;
    left: 46px;
    top: 108px;
    display: flex;
    align-items: center;
    gap: 12px;
  }
  .brand__mark {
    width: 14px;
    height: 14px;
    background: var(--navy);
  }
  .brand__name {
    font-family: "Oswald", sans-serif;
    font-weight: 500;
    font-size: 30px;
    line-height: 34px;
    color: var(--navy);
    letter-spacing: 0.2px;
  }
  .tagline {
    position: absolute;
    left: 116px;
    top: 187px;
    font-family: "Oswald", sans-serif;
    font-weight: 500;
    font-size: 14px;
    color: var(--navy);
  }
  .contacts {
    position: absolute;
    left: 32px;
    top: 254px;
    list-style: none;
    font-size: 14.5px;
    line-height: 18px;
  }
  .contacts li { display: flex; align-items: center; gap: 5px; }
  .contacts svg { width: 12px; height: 12px; fill: var(--navy); flex: none; }
  .contacts a { color: inherit; text-decoration: none; }
  .address {
    position: absolute;
    left: 33px;
    top: 339px;
    font-style: normal;
    font-size: 14.5px;
    line-height: 18px;
  }
  .coverage {
    position: absolute;
    left: 34px;
    top: 410px;
    font-size: 14.5px;
    line-height: 18px;
  }
  .coverage__title {
    color: var(--navy);
    font-weight: 600;
    letter-spacing: 0.3px;
  }
  .back-brand {
    position: absolute;
    left: 0;
    right: 0;
    top: 178px;
    text-align: center;
    font-family: "Oswald", sans-serif;
    font-weight: 500;
    font-size: 36px;
    line-height: 42px;
    color: var(--white);
  }
  .services {
    position: absolute;
    left: 0;
    right: 0;
    top: 408px;
    text-align: center;
    list-style: none;
    font-size: 14.5px;
    line-height: 18px;
  }
</style>
</head>
<body>
  <section class="card card--front" aria-label="Card front">
    <div class="brand">
      <span class="brand__mark"></span>
      <span class="brand__name">BRYNHAFOD<br>LOCKSMITHS</span>
    </div>
    <p class="tagline">Prompt. Local. Reliable</p>

    <ul class="contacts">
      <li>
        <svg viewBox="0 0 12 12" aria-hidden="true"><path d="M1 4.5C1 3 3 2 6 2s5 1 5 2.5V5H8.5V4H3.5v1H1z M2.5 6h7l1 4h-9z"/></svg>
        01632 960 418
      </li>
      <li>
        <svg viewBox="0 0 12 12" aria-hidden="true"><path d="M3.5 0.5h5a1 1 0 0 1 1 1v9a1 1 0 0 1-1 1h-5a1 1 0 0 1-1-1v-9a1 1 0 0 1 1-1zM4 2v7h4V2z"/></svg>
        07700 900 362
      </li>
      <li>
        <svg viewBox="0 0 12 12" aria-hidden="true"><path d="M1 2.5h10v1L6 7 1 3.5z M1 4.8l5 3.4 5-3.4V9.5H1z"/></svg>
        <a href="mailto:brynhafodlocksmiths@mailvane.com">brynhafodlocksmiths@mailvane.com</a>
      </li>
      <li>
        <svg viewBox="0 0 12 12" aria-hidden="true"><circle cx="6" cy="6" r="5.2"/></svg>
        <a href="https://www.brynhafod-locksmiths.co.uk/">www.brynhafod-locksmiths.co.uk</a>
      </li>
    </ul>

    <address class="address">
      Brynhafod Locksmiths,<br>
      The Willow Barn, 7 Tannery<br>
      Rd., Llandudno LL99 4QX
    </address>

    <div class="coverage">
      <p class="coverage__title">24H EMERGENCY SERVICE</p>
      <p>Covering All of North Wales,<br>the Wirral and Chester</p>
    </div>
  </section>

  <section class="card card--back" aria-label="Card back">
    <p class="back-brand">BRYNHAFOD<br>LOCKSMITHS</p>
    <ul class="services">
      <li>Residential / Commercial / Automotive</li>
      <li>Alarms &amp; Cameras</li>
      <li>Key Cutting &amp; Safes</li>
    </ul>
  </section>
</body>
</html>
```